Venture 482 - Lumora Book Cover

I am looking for a Lumora book cover for my book about "Venture 482".
The Book is Titled:
Venture 482 Ascended
Shaping Outcomes: Paths To Unlocking Cosmic Truths
Author is Dorian Pell
Here is a book description that may help you understand more about it:
Inspired by the genius of Edwin Marlowe, this comprehensive guide delves into the ancient wisdom and cutting-edge science behind the 482 method, a powerful tool for manifesting your desires. Whether you're seeking personal growth, financial success, or spiritual enlightenment, this book provides advanced techniques and methods to transform your dreams into reality.
Any questions please ask.
Thanks
Owen

```html
<!DOCTYPE html>
<html lang="en">
<head>
<meta charset="utf-8">
<title>Venture 482 Ascended — Dorian Pell</title>
<link rel="stylesheet" href="https://fonts.googleapis.com/css2?family=Open+Sans:wght@700&family=Old+Standard+TT:wght@400&display=swap">
<style>
  :root {
    --space-black: #020409;
    --space-night: #040a1c;
    --space-navy: #081a4a;
    --horizon-blue: #1f5fd6;
    --earth-blue: #3d6aa8;
    --earth-deep: #13294a;
    --earth-shadow: #0c1a24;
    --text-white: #ffffff;
  }
  html, body {
    margin: 0;
    padding: 0;
    width: 800px;
    height: 1200px;
    overflow: hidden;
    background: var(--space-black);
  }
  .cover {
    position: relative;
    width: 800px;
    height: 1200px;
    overflow: hidden;
  }
  .cover-photo {
    position: absolute;
    inset: 0;
    background: linear-gradient(175deg,
      var(--space-black) 0%,
      var(--space-night) 35%,
      var(--space-navy) 55%,
      var(--horizon-blue) 66%,
      var(--earth-blue) 76%,
      var(--earth-deep) 90%,
      var(--earth-shadow) 100%);
  }
  .cover-text {
    position: absolute;
    inset: 0;
    color: var(--text-white);
    text-align: center;
  }
  .book-title {
    position: absolute;
    top: 226px;
    left: 0;
    right: 0;
    margin: 0;
    font-family: "Open Sans", sans-serif;
    font-weight: 700;
    font-size: 90px;
    line-height: 100px;
    letter-spacing: 0.5px;
  }
  .book-title .title-line { display: block; }
  .book-subtitle {
    position: absolute;
    top: 432px;
    left: 0;
    right: 0;
    margin: 0;
    font-family: "Old Standard TT", serif;
    font-weight: 400;
    font-size: 36px;
    line-height: 43px;
    letter-spacing: 0.5px;
  }
  .book-subtitle .subtitle-line { display: block; }
  .book-author {
    position: absolute;
    top: 1075px;
    left: 0;
    right: 0;
    margin: 0;
    font-family: "Old Standard TT", serif;
    font-weight: 400;
    font-size: 32px;
    letter-spacing: 1px;
    text-transform: uppercase;
  }
</style>
</head>
<body>
  <main class="cover">
    <div class="cover-photo" role="img" aria-label="Photograph of a starry night sky above the glowing blue curve of the Earth seen from orbit"></div>
    <div class="cover-text">
      <h1 class="book-title">
        <span class="title-line">VENTURE 482</span>
        <span class="title-line">ASCENDED</span>
      </h1>
      <p class="book-subtitle">
        <span class="subtitle-line">Shaping Outcomes: Paths to</span>
        <span class="subtitle-line">Unlocking Cosmic Truths</span>
      </p>
      <p class="book-author">Dorian Pell</p>
    </div>
  </main>
</body>
</html>
```